Business Card Design

New business card design

Target Market(s)

Residential & Commercial Property Managers

Industry/Entity Type

Plumbing Services

Contact Information for Business Card

Name - Rowan Keddle, title - Director, Phone Number - 0431 286 517, email - rowan@tbk-plumbing.com.au, Company ABN - 73 215 904 386,

Font styles to use
Sans Serif

Colors
0054AA
0677BA
7BADD7
CADEEF
E8F1F8

```html
<!DOCTYPE html>
<html lang="en">
<head>
<meta charset="utf-8">
<title>TBK Plumbing Services – Business Card</title>
<link rel="stylesheet" href="https://fonts.googleapis.com/css2?family=Poppins:wght@300;400;500&display=swap">
<style>
  :root {
    --backdrop: #232323;
    --card-dark: #1a1f25;
    --brand-blue: #29a9e1;
    --brand-blue-deep: #1a8dc4;
    --text-light: #e6e6e6;
    --text-muted: #8a8a8a;
    --surname: #7d766c;
  }
  * { margin: 0; padding: 0; box-sizing: border-box; }
  html, body {
    width: 1200px; height: 780px; overflow: hidden;
    background: var(--backdrop);
    font-family: "Poppins", sans-serif;
  }
  .canvas { position: relative; width: 1200px; height: 780px; }

  .card {
    position: absolute; top: 235px;
    width: 520px; height: 310px;
    border-radius: 22px; overflow: hidden;
    box-shadow: 0 18px 40px rgba(0,0,0,.55);
  }

  /* Front */
  .card-front { left: 50px; background: var(--card-dark); }
  .accent-bar {
    position: absolute; left: 0; top: 40px;
    width: 9px; height: 100px; background: var(--brand-blue);
  }
  .brand {
    position: absolute; left: 36px; top: 58px;
    display: flex; align-items: center; gap: 10px;
  }
  .brand-dot { width: 12px; height: 12px; border-radius: 50%; background: var(--brand-blue); }
  .brand-name {
    font-weight: 300; font-size: 26px; color: var(--text-light);
    letter-spacing: 1px; white-space: nowrap;
  }
  .divider { position: absolute; left: 0; top: 0; }
  .abn {
    position: absolute; left: 36px; bottom: 38px;
    font-size: 12px; font-weight: 300; color: var(--brand-blue);
    letter-spacing: .5px;
  }
  .contact-block { position: absolute; left: 268px; top: 132px; }
  .person-name { font-size: 26px; font-weight: 300; line-height: 1; white-space: nowrap; }
  .person-name .first { color: var(--brand-blue); font-weight: 500; }
  .person-name .last { color: var(--surname); }
  .person-title { font-size: 12px; color: var(--text-light); margin: 4px 0 14px; }
  .contact-list { list-style: none; }
  .contact-list li {
    display: flex; align-items: center; gap: 8px;
    font-size: 11.5px; font-weight: 300; color: var(--text-light);
    line-height: 20px;
  }
  .contact-list svg { width: 11px; height: 11px; flex: none; }
  .edge-bar {
    position: absolute; right: 0; bottom: 28px;
    width: 9px; height: 110px; background: var(--brand-blue);
  }

  /* Back */
  .card-back {
    left: 630px; background: var(--brand-blue);
    display: flex; align-items: center; justify-content: center;
  }
  .card-back .brand-name {
    font-size: 38px; color: var(--brand-blue-deep); font-weight: 300;
  }
  .card-back .brand { position: static; gap: 14px; }
  .card-back .brand-dot { width: 16px; height: 16px; background: #ffffff; }
</style>
</head>
<body>
<main class="canvas">

  <section class="card card-front" aria-label="Business card front">
    <div class="accent-bar"></div>
    <div class="brand">
      <span class="brand-name">tbk plumbing services</span>
      <span class="brand-dot"></span>
    </div>
    <svg class="divider" width="520" height="310" aria-hidden="true">
      <line x1="250" y1="120" x2="150" y2="240" stroke="var(--brand-blue)" stroke-width="1"/>
    </svg>
    <p class="abn">ABN - 73 215 904 386</p>

    <div class="contact-block">
      <p class="person-name"><span class="first">Rowan</span> <span class="last">Keddle</span></p>
      <p class="person-title">Director</p>
      <ul class="contact-list">
        <li>
          <svg viewBox="0 0 12 12" aria-hidden="true"><path d="M2.5 1l2 2.3-1 1.2a6 6 0 0 0 4 4l1.2-1 2.3 2-1.3 1.8C5.5 11.4.6 6.5 1 2.3z" fill="var(--brand-blue)"/></svg>
          0431 286 517
        </li>
        <li>
          <svg viewBox="0 0 12 12" aria-hidden="true"><rect x="1" y="2.5" width="10" height="7" rx="1" fill="var(--brand-blue)"/><path d="M1.5 3l4.5 3.5L10.5 3" stroke="var(--card-dark)" fill="none"/></svg>
          www.tbk-plumbing.com.au
        </li>
        <li>
          <svg viewBox="0 0 12 12" aria-hidden="true"><circle cx="6" cy="6" r="5" fill="var(--brand-blue)"/><path d="M1 6h10M6 1c-2.5 3-2.5 7 0 10M6 1c2.5 3 2.5 7 0 10" stroke="var(--card-dark)" stroke-width=".7" fill="none"/></svg>
          rowan@tbk-plumbing.com.au
        </li>
      </ul>
    </div>
    <div class="edge-bar"></div>
  </section>

  <section class="card card-back" aria-label="Business card back">
    <div class="brand">
      <span class="brand-name">tbk plumbing services</span>
      <span class="brand-dot"></span>
    </div>
  </section>

</main>
</body>
</html>
```